Small boutique home based travel agency needs a flyer design and logo

I need a flyer design for my boutique home-based travel agency that specializes in designing personalized trips to Europe, ocean and river cruises and escorted small group tours to exotic destinations.

We are travel experts, provide the best customer service in the industry and would like this promoted. Open by appointment.
Would like the flyer and logo to use a globe and I like color. Please integrate photo.

Boutique

```html
<!DOCTYPE html>
<html lang="en">
<head>
<meta charset="utf-8">
<title>Meridian Travel – Destinations Flyer</title>
<link href="https://fonts.googleapis.com/css2?family=Source+Sans+3:wght@400;600&family=Oswald:wght@500;600&family=Gochi+Hand&display=swap" rel="stylesheet">
<style>
  :root{
    --royal:#1f4f97;
    --royal-light:#2b5fa8;
    --orange:#f37021;
    --green:#12a84a;
    --white:#ffffff;
    --page:#ffffff;
  }
  *{box-sizing:border-box;margin:0;padding:0}
  html,body{width:1200px;height:927px;overflow:hidden;background:var(--page)}
  .flyer{position:relative;width:1200px;height:927px;background:var(--page);font-family:"Source Sans 3",Arial,sans-serif;color:var(--white)}
  .panel{position:absolute;left:27px;top:27px;width:1148px;height:712px;background:var(--royal)}
  .world-map{position:absolute;inset:0;background:radial-gradient(ellipse at 50% 45%,var(--royal-light) 0%,var(--royal) 70%)}
  .column{position:absolute;top:22px;font-size:13.2px;line-height:17px;text-align:justify}
  .column--left{left:34px;width:532px}
  .column--right{left:602px;width:538px}
  .section-title{display:inline-block;font-family:"Oswald",Arial,sans-serif;font-weight:600;font-size:15px;letter-spacing:.3px;line-height:17px;text-transform:uppercase;padding-right:8px;border-bottom:2px solid var(--orange);border-right:2px solid var(--orange);margin-bottom:1px}
  .column p{margin-bottom:17px}
  .column .section-title + p{margin-top:0}
  .tagline{font-family:"Oswald",Arial,sans-serif;font-weight:500;font-size:20px;color:var(--orange);margin:-2px 0 8px;text-align:left}
  .testimonial{background:var(--orange);padding:12px 16px 8px 16px;font-family:"Gochi Hand",cursive;font-size:16.5px;line-height:20px;text-transform:uppercase;text-align:left;height:110px}
  .testimonial cite{display:block;text-align:right;font-style:normal;margin-top:10px}
  .flight-path{position:absolute;left:14px;top:709px;width:610px;height:24px}
  .gallery{position:absolute;left:27px;top:755px;width:1173px;height:142px}
  .gallery > div{position:absolute;top:0;height:142px}
  .bar--blue{background:var(--royal)}
  .bar--orange{background:var(--orange)}
  .bar--green{background:var(--green)}
  .photo-harbour{background:linear-gradient(180deg,#9cc4e6 0%,#c9a27a 55%,#3f6f9a 100%)}
  .photo-cathedral{background:linear-gradient(180deg,#7fb0e0 0%,#e6e0d2 55%,#5f8c3c 100%)}
  .photo-statue{background:linear-gradient(180deg,#6f7f56 0%,#d6d1c6 50%,#4c5a3a 100%)}
  .photo-gate{background:linear-gradient(180deg,#a9cbe9 0%,#cfc5b2 60%,#7d7a6a 100%)}
  .photo-coast{background:linear-gradient(180deg,#9dc6ea 0%,#e5e2d8 45%,#2c6ea8 100%)}
</style>
</head>
<body>
<main class="flyer">
  <section class="panel">
    <div class="world-map" role="img" aria-label="Faint world map behind the text"></div>

    <div class="column column--left">
      <h2 class="section-title">European Vacations</h2>
      <p>For your European vacation, Meridian can create your own detailed day-to-day itinerary. Our travel experience and insider knowledge means the very best experiences for you. Relax and have fun- we do the rest!</p>
      <p>For group tours, we work with the top tour operators and will match you to the tour that is just right for you. Castles in Scotland? Pubs in Ireland? Shopping and art in Paris? The list is endless!</p>
      <p>At Meridian, we believe that immersing yourself in travel should delight, encourage, refresh-and-at journey's end, send you home with a new perspective on your own corner of the world.</p>
      <p>Imagine a breathtaking vista of green grass and beautiful thatched cottages in the Cotswolds. Wake each morning knowing a brand new experience is in front of you. That is what traveling is all about!</p>
      <h2 class="section-title">Mexico</h2>
      <p>Romantic honeymoon or anniversary? Family vacation? Fishing and Golf?</p>
      <p>Meridian can plan your vacation to sunny Mexico be it a boutique, adult-only retreat or an incredible family friendly ocean-front resort. There is a place for everyone in Mexico!</p>
      <h2 class="section-title">Hawaii</h2>
      <p>At Meridian we are destination specialists on each unique Hawaiian Island. Is it volcanoes, orchids, macadamia nut farms and incredible snorkeling that interest you? We will send you to Hawaii Island." Perhaps the quiet and lush island of Kauai is your style. Surf and fun in Waikiki? Oahu is the place for you and then of course Maui no ka oi!</p>
      <p>Whatever your desires are in Paradise, we will make them happen!</p>
    </div>

    <div class="column column--right">
      <h2 class="section-title">Cruises</h2>
      <p>At Meridian our goal is to match each client to the perfect cruise for them. Your perfect cruise will be the destination you want, the size of ship you prefer, your price-point and what you love to do. There is a cruise for everyone and it is a fun way to travel!</p>
      <h2 class="section-title">River Cruising - A Better Way to Explore</h2>
      <p>A river cruise is a cultural experience into the very heart of the world's greatest cities and most charming towns. Where else but on a river cruise can you travel gently along on an elegant, intimate ship, docking in the center of town, strolling off to begin your exploration? Travel with ease, unpack once and enjoy ever changing.</p>
      <p>Call us to plan one of these delightful cruises!</p>
      <h2 class="section-title">Escorted Small-Group Tours</h2>
      <p>Each year Meridian offers several escorted, small-group tours to interesting destinations in the US and abroad. Our escorted tours offer intangible benefits and unique perspectives, new friendships and shared experiences. These tours are great for couples, friends traveling together or single-travelers who prefer not to travel alone.</p>
      <p>Escorted Small-Group Tours designed for your church, club or family and friends Meridian designs and escorts small-group tours just for your private group. Call me to talk about this great opportunity!</p>
      <p class="tagline">Our passion is sharing the wonders of the world with you</p>
      <blockquote class="testimonial">
        "We had an extremely fun-filled and problem-free vacation. Thank you for being the planner and master technician for a flawless itinerary."
        <cite>R&amp;J Calloway, Hood River, Oregon</cite>
      </blockquote>
    </div>
  </section>

  <svg class="flight-path" viewBox="0 0 610 24" aria-hidden="true">
    <line x1="30" y1="12" x2="610" y2="12" stroke="#f37021" stroke-width="2.5"/>
    <path d="M4 12 L30 9 L36 12 L30 15 Z M14 11 L22 2 L26 2 L21 11 Z M14 13 L22 22 L26 22 L21 13 Z M5 12 L3 7 L6 7 L9 11 Z M5 12 L3 17 L6 17 L9 13 Z" fill="#f37021"/>
  </svg>

  <section class="gallery">
    <div class="bar--blue" style="left:0;width:41px"></div>
    <div class="photo-harbour" style="left:49px;width:184px" role="img" aria-label="Photo of a colourful Mediterranean harbour town"></div>
    <div class="bar--orange" style="left:243px;width:41px"></div>
    <div class="photo-cathedral" style="left:296px;width:150px" role="img" aria-label="Photo of the cathedral and leaning tower in Pisa"></div>
    <div class="bar--green" style="left:455px;width:41px"></div>
    <div class="photo-statue" style="left:505px;width:137px" role="img" aria-label="Photo of a classical Roman statue"></div>
    <div class="bar--blue" style="left:655px;width:41px"></div>
    <div class="photo-gate" style="left:706px;width:188px" role="img" aria-label="Photo of a monumental stone gate in a European city"></div>
    <div class="bar--orange" style="left:906px;width:40px"></div>
    <div class="photo-coast" style="left:955px;width:185px" role="img" aria-label="Photo of a coastal watchtower above the sea"></div>
    <div class="bar--green" style="left:1149px;width:24px"></div>
  </section>
</main>
</body>
</html>
```